TA BRAMLEY BUSINESS CARD DESIGN PROJECT

We need to utilize our logo that was expertly created on PixelHarbor and now need to match this with a business card design.

```html
<!DOCTYPE html>
<html lang="en">
<head>
<meta charset="utf-8">
<title>TA BRAMLEY Business Card</title>
<link href="https://fonts.googleapis.com/css2?family=Montserrat:wght@400;500;700;800&display=swap" rel="stylesheet">
<style>
  :root {
    --page-bg: #e6e1d9;
    --card-bg: #f5f2ed;
    --brand-blue: #0f4c96;
    --brand-blue-deep: #0b3a76;
    --brand-blue-light: #2a6cb5;
    --text-light: #eef3fa;
    --text-soft: #d6e2f1;
    --accent-tab: #f1ebe0;
  }
  * { margin: 0; padding: 0; box-sizing: border-box; }
  html, body {
    width: 1200px; height: 1047px; overflow: hidden;
    background: var(--page-bg);
    font-family: "Montserrat", sans-serif;
  }
  .card {
    position: absolute; left: 150px; top: 290px;
    width: 950px; height: 518px;
    border-radius: 24px; overflow: hidden;
    background: var(--card-bg);
    box-shadow: 0 10px 30px rgba(60, 50, 40, 0.18);
  }
  .card-panel { position: absolute; inset: 0; width: 100%; height: 100%; }
  .name-tab {
    position: absolute; left: 0; top: 115px;
    width: 30px; height: 64px; background: var(--accent-tab);
  }
  .identity { position: absolute; left: 45px; top: 110px; color: var(--text-light); white-space: nowrap; }
  .person-name { font-weight: 700; font-size: 32px; letter-spacing: 1px; line-height: 38px; }
  .person-role { font-weight: 500; font-size: 23px; line-height: 30px; color: var(--text-soft); margin-top: 2px; }
  .contacts { position: absolute; left: 55px; top: 209px; list-style: none; color: var(--text-light); white-space: nowrap; }
  .contacts li { display: flex; align-items: center; font-size: 22px; font-weight: 500; height: 33px; }
  .contacts svg { width: 18px; height: 18px; margin-right: 8px; fill: var(--text-light); }
  .address {
    position: absolute; left: 40px; top: 335px;
    font-size: 22px; font-weight: 500; line-height: 33px; color: var(--text-soft); white-space: nowrap;
  }
  .wordmark {
    position: absolute; left: 489px; top: 226px; width: 440px;
    text-align: center; white-space: nowrap;
    font-weight: 800; font-size: 46px; line-height: 58px; letter-spacing: 4px;
    color: var(--brand-blue);
  }
</style>
</head>
<body>
  <div class="card">
    <svg class="card-panel" viewBox="0 0 950 518" preserveAspectRatio="none" aria-hidden="true">
      <defs>
        <linearGradient id="panelGradient" x1="0" y1="0" x2="1" y2="1">
          <stop offset="0" stop-color="var(--brand-blue-light)"/>
          <stop offset="0.6" stop-color="var(--brand-blue)"/>
          <stop offset="1" stop-color="var(--brand-blue-deep)"/>
        </linearGradient>
      </defs>
      <path d="M0 0 H520 Q400 259 520 518 H0 Z" fill="url(#panelGradient)"/>
    </svg>

    <div class="name-tab"></div>
    <div class="identity">
      <div class="person-name">OWEN HARTLEY</div>
      <div class="person-role">Managing Director</div>
    </div>

    <ul class="contacts">
      <li><svg viewBox="0 0 24 24"><path d="M6.6 10.8a15 15 0 0 0 6.6 6.6l2.2-2.2c.3-.3.7-.4 1-.2 1.1.4 2.3.6 3.6.6.6 0 1 .4 1 1V20c0 .6-.4 1-1 1A17 17 0 0 1 3 4c0-.6.4-1 1-1h3.5c.6 0 1 .4 1 1 0 1.3.2 2.5.6 3.6.1.3 0 .7-.2 1z"/></svg>123 456 789</li>
      <li><svg viewBox="0 0 24 24"><path d="M3 6h18v1.5l-9 6-9-6z M3 9.5l9 6 9-6V18H3z"/></svg>info@yourmail.com</li>
      <li><svg viewBox="0 0 24 24"><path d="M12 3a9 9 0 1 0 0 18 9 9 0 0 0 0-18zm0 2c1 1.5 1.8 3.5 2 6h-4c.2-2.5 1-4.5 2-6zm-2 8h4c-.2 2.5-1 4.5-2 6-1-1.5-1.8-3.5-2-6z"/></svg>www.yourwebsite.com</li>
    </ul>

    <div class="address">Your address, City<br>State, Zip 1234</div>

    <div class="wordmark">TA BRAMLEY</div>
  </div>
</body>
</html>
```